Website for Excavator and Earthworks Company

We require a modern, sleek and practical website for our newly created earthworks/excavator business in Perth, Western Australia called Bluegum Ridge Earthworks.

The website should have a modern, cutting edge feel but only needs to be relatively simplistic in it's layout and eventual functionality.

Some pages it should have would be Home, About, Projects and Contact Us.

```html
<!DOCTYPE html>
<html lang="en">
<head>
<meta charset="utf-8">
<title>Bluegum Ridge Earthworks</title>
<link href="https://fonts.googleapis.com/css2?family=Saira+Condensed:wght@600;700;800&family=Barlow:wght@400;500;600&family=Dancing+Script:wght@600&display=swap" rel="stylesheet">
<style>
:root{
  --lime:#c8dc00;
  --dark:#1c2025;
  --ink:#111214;
  --footer:#15181b;
  --white:#ffffff;
  --muted:#d7d9dc;
  --head:"Saira Condensed",sans-serif;
  --body:"Barlow",sans-serif;
}
*{margin:0;padding:0;box-sizing:border-box}
html,body{width:1200px;height:3236px;overflow:hidden}
body{position:relative;background:var(--white);font-family:var(--body);color:var(--ink)}
.abs{position:absolute}
.head{font-family:var(--head);font-weight:800;text-transform:uppercase;line-height:1}

/* brand */
.brand{font-family:var(--head);font-weight:800;color:var(--white);font-size:19px;letter-spacing:.5px;text-transform:uppercase;display:flex;align-items:center;gap:8px;white-space:nowrap}
.brand-dot{width:14px;height:14px;background:var(--lime)}
.header-brand{left:113px;top:25px}
.footer-brand{left:113px;top:3044px}

/* header */
.site-header{left:0;top:0;width:1200px;height:75px;background:var(--dark)}
.nav{left:416px;top:32px;display:flex;gap:30px;font-family:var(--head);font-weight:700;font-size:12px;color:var(--white);text-transform:uppercase}
.nav .active{color:var(--lime);border-bottom:2px solid var(--lime);padding-bottom:2px}
.header-phone{left:744px;top:24px;display:flex;align-items:center;gap:9px;color:var(--white);font-family:var(--head);font-weight:700;font-size:20px;letter-spacing:1px}
.icon-circle{width:26px;height:26px;border-radius:50%;background:#3b4148;display:flex;align-items:center;justify-content:center}
.header-cta{left:949px;top:21px;width:139px;height:33px;background:var(--lime);clip-path:polygon(0 0,88% 0,100% 100%,12% 100%);font-family:var(--head);font-weight:700;font-size:12px;display:flex;align-items:center;justify-content:center;text-transform:uppercase}

/* hero */
.hero{left:0;top:75px;width:1200px;height:590px;background:linear-gradient(180deg,#3f66a8 0%,#8fb2dc 35%,#4e6b3a 60%,#3c4e2b 100%)}
.hero-shade{left:0;top:75px;width:700px;height:590px;background:linear-gradient(90deg,rgba(20,35,60,.8),rgba(20,35,60,0))}
.hero-eyebrow{left:112px;top:170px;color:var(--white);font-family:var(--head);font-weight:700;font-size:15px;text-transform:uppercase;display:flex;align-items:center;gap:6px}
.hero-eyebrow i{display:block;width:50px;height:3px;background:var(--lime)}
.hero-title{left:110px;top:204px;color:var(--white);font-size:71px;line-height:.99}
.hero-title span{color:var(--lime)}
.hero-text{left:112px;top:500px;width:310px;color:var(--white);font-size:12px;line-height:1.6}
.play{left:932px;top:538px;display:flex;align-items:center;gap:12px}
.play-btn{width:66px;height:66px;border-radius:50%;border:4px solid rgba(255,255,255,.35);background:#2b2f22;display:flex;align-items:center;justify-content:center}
.play-label{font-family:"Dancing Script",cursive;color:var(--white);font-size:22px}

/* section titles */
.eyebrow{display:flex;align-items:center;justify-content:center;gap:6px;font-size:10px;text-transform:uppercase;width:1200px;left:0}
.eyebrow i{display:block;width:45px;height:2px;background:var(--ink)}
.section-title{left:0;width:1200px;text-align:center;font-size:38px}

/* services */
.side-band{left:0;top:888px;width:247px;height:300px;background:var(--lime)}
.side-word{left:-5px;top:890px;width:100px;height:805px;overflow:hidden}
.side-word span{display:block;transform:rotate(90deg) translateY(-100%);transform-origin:0 0;position:absolute;left:0;top:0;white-space:nowrap;font-family:var(--head);font-weight:800;font-size:100px;color:transparent;-webkit-text-stroke:1px rgba(255,255,255,.45);line-height:1}
.service-card{top:803px;width:314px;height:319px;overflow:hidden}
.service-card .photo{position:absolute;inset:0}
.service-card .fade{position:absolute;inset:0;background:linear-gradient(180deg,rgba(0,0,0,0) 50%,rgba(0,0,0,.85) 100%)}
.service-card h3{position:absolute;left:24px;bottom:17px;color:var(--white);font-size:19px;line-height:1.3}
.corner{position:absolute;right:0;bottom:0;width:68px;height:66px;background:var(--lime);clip-path:polygon(100% 0,100% 100%,0 100%)}
.corner-arrow{position:absolute;right:10px;bottom:9px;width:22px;height:22px;border-radius:50%;background:var(--white);display:flex;align-items:center;justify-content:center}

/* about */
.about{left:0;top:1186px;width:1200px;height:509px;background:var(--lime)}
.about-photo{left:601px;top:1186px;width:599px;height:429px;background:linear-gradient(135deg,#b38a3a 0%,#7d6a4a 45%,#cfd2d6 100%)}
.about-stripe{left:790px;top:1615px;width:230px;height:80px;background:var(--ink);clip-path:polygon(0 0,30% 0,100% 100%,70% 100%)}
.about-stripe2{left:930px;top:1615px;width:270px;height:80px;background:linear-gradient(90deg,#8a6e52,#6b5a48);clip-path:polygon(0 0,100% 0,100% 100%,35% 100%)}
.about-eyebrow{left:112px;top:1276px;font-size:10px;display:flex;align-items:center;gap:6px;text-transform:uppercase}
.about-eyebrow i{display:block;width:50px;height:1px;background:var(--ink)}
.about-title{left:112px;top:1302px;font-size:40px;line-height:1.15}
.about-text{left:112px;top:1443px;width:390px;font-size:11px;line-height:1.5}
.btn-dark{left:113px;top:1539px;width:224px;height:42px;background:var(--ink);clip-path:polygon(0 0,90% 0,100% 100%,10% 100%);color:var(--white);font-family:var(--head);font-weight:700;font-size:13px;display:flex;align-items:center;justify-content:center;text-transform:uppercase}

/* projects */
.project{width:366px;height:243px}
.project-tag{position:absolute;left:0;top:0;background:var(--ink);color:var(--white);font-family:var(--head);font-weight:700;font-size:11px;padding:3px 8px 3px 19px;text-transform:uppercase}
.btn-lime{left:498px;top:2350px;width:203px;height:40px;background:var(--lime);clip-path:polygon(0 0,88% 0,100% 100%,12% 100%);font-family:var(--head);font-weight:700;font-size:13px;display:flex;align-items:center;justify-content:center;text-transform:uppercase}

/* contact */
.contact-lime{left:594px;top:2448px;width:606px;height:551px;background:var(--lime)}
.contact-word{left:0;top:2448px;width:594px;height:140px;overflow:hidden;font-family:var(--head);font-weight:800;font-size:170px;color:#ececec;line-height:1;letter-spacing:4px;white-space:nowrap}
.contact-lime-low{left:324px;top:2919px;width:340px;height:80px;background:var(--lime)}
.contact-photo{left:0;top:2582px;width:660px;height:337px;background:linear-gradient(110deg,#c9c8b8 0%,#9aa09a 40%,#c77a55 70%,#7c7a78 100%)}
.contact-title{left:680px;top:2505px;width:408px;text-align:right;font-size:36px;line-height:1.27}
.field{left:721px;width:367px;height:34px;border:1px solid rgba(17,18,20,.45);font-size:11px;padding:9px 13px;color:#3a3f20}
.submit{left:721px;top:2906px;width:367px;height:41px;background:var(--ink);clip-path:polygon(0 0,94% 0,100% 100%,6% 100%);color:var(--white);font-family:var(--head);font-weight:700;font-size:13px;display:flex;align-items:center;justify-content:center;text-transform:uppercase}

/* footer */
.site-footer{left:0;top:2999px;width:1200px;height:237px;background:var(--footer)}
.footer-about{left:112px;top:3114px;width:200px;font-size:8px;line-height:1.9;color:var(--muted)}
.footer-rule{top:3037px;width:1px;height:142px;background:#30353b}
.footer-head{top:3040px;font-family:var(--head);font-weight:700;font-size:14px;text-transform:uppercase;color:var(--white)}
.footer-head i{display:block;width:20px;height:2px;background:var(--lime);margin-top:4px}
.footer-list{font-size:8px;line-height:2.2;color:var(--muted);list-style:none}
.footer-item{display:flex;align-items:center;gap:8px;font-size:8px;color:var(--muted);height:26px;white-space:nowrap}
.footer-item .dot{width:18px;height:18px;border-radius:50%;background:var(--white)}
.footer-bottom{left:112px;top:3191px;width:976px;border-top:1px solid #30353b;padding-top:13px;display:flex;justify-content:space-between;font-size:8px;color:var(--muted)}
</style>
</head>
<body>

<header class="abs site-header"></header>
<div class="abs brand header-brand"><span class="brand-dot"></span>Bluegum Ridge</div>
<nav class="abs nav"><span class="active">Home</span><span>About Us</span><span>Projects</span><span>Contact Us</span></nav>
<div class="abs header-phone"><span class="icon-circle"><svg width="12" height="12" viewBox="0 0 24 24"><path fill="#c8dc00" d="M6.6 10.8a15 15 0 0 0 6.6 6.6l2.2-2.2c.3-.3.7-.4 1-.2 1.1.4 2.3.6 3.6.6.6 0 1 .4 1 1V20c0 .6-.4 1-1 1A17 17 0 0 1 3 4c0-.6.4-1 1-1h3.5c.6 0 1 .4 1 1 0 1.3.2 2.5.6 3.6.1.3 0 .7-.2 1z"/></svg></span>+61 400 555 218</div>
<div class="abs header-cta">Contact Us</div>

<section>
  <div class="abs hero" role="img" aria-label="Yellow mini excavator on a grassy site under blue sky"></div>
  <div class="abs hero-shade"></div>
  <p class="abs hero-eyebrow">Welcome to Bluegum Ridge Earthworks. <i></i></p>
  <h1 class="abs head hero-title">Precision<br>Earthworks,<br>Powered by<br><span>Experience</span></h1>
  <p class="abs hero-text">Bluegum Ridge Earthworks delivers expert excavation and site preparation services across Perth and Western Australia, combining cutting-edge machinery with trusted workmanship.</p>
  <div class="abs play"><span class="play-btn"><svg width="22" height="24" viewBox="0 0 22 24"><path d="M2 1l19 11L2 23z" fill="#c8dc00"/></svg></span><span class="play-label">Play Now</span></div>
</section>

<section>
  <div class="abs side-band"></div>
  <p class="abs eyebrow" style="top:720px"><i></i>Services<i></i></p>
  <h2 class="abs head section-title" style="top:738px">Bluegum Ridge Earthworks Services</h2>

  <article class="abs service-card" style="left:112px">
    <div class="photo" role="img" aria-label="Residential construction site with excavator" style="background:linear-gradient(180deg,#9bb8d0,#6f8a5a 45%,#6d5a44)"></div>
    <div class="fade"></div>
    <h3 class="head">Civil &amp; Residential<br>Earthworks</h3>
    <div class="corner"></div><span class="corner-arrow"><svg width="10" height="10" viewBox="0 0 10 10"><path d="M1 5h8M6 2l3 3-3 3" stroke="#111" fill="none" stroke-width="1.2"/></svg></span>
  </article>
  <article class="abs service-card" style="left:442px">
    <div class="photo" role="img" aria-label="Orange excavators levelling bare land" style="background:linear-gradient(180deg,#c7d3dc,#b08a5e 45%,#8a6843)"></div>
    <div class="fade"></div>
    <h3 class="head">Land Levelling<br>&amp; Preparation</h3>
    <div class="corner"></div><span class="corner-arrow"><svg width="10" height="10" viewBox="0 0 10 10"><path d="M1 5h8M6 2l3 3-3 3" stroke="#111" fill="none" stroke-width="1.2"/></svg></span>
  </article>
  <article class="abs service-card" style="left:773px">
    <div class="photo" role="img" aria-label="Excavated quarry face with green vegetation" style="background:linear-gradient(180deg,#dfe8ef,#4f7a3a 30%,#8b7866 60%,#5f5e64)"></div>
    <div class="fade"></div>
    <h3 class="head">Bulk Excavation &amp;<br>Site Clearing</h3>
    <div class="corner"></div><span class="corner-arrow"><svg width="10" height="10" viewBox="0 0 10 10"><path d="M1 5h8M6 2l3 3-3 3" stroke="#111" fill="none" stroke-width="1.2"/></svg></span>
  </article>
</section>

<section>
  <div class="abs about"></div>
  <div class="abs side-word"><span>BLUEGUM RIDGE</span></div>
  <div class="abs about-photo" role="img" aria-label="Worker in hard hat and hi-vis vest standing on an excavator"></div>
  <div class="abs about-stripe"></div>
  <div class="abs about-stripe2" role="img" aria-label="Soil ground texture"></div>
  <p class="abs about-eyebrow">About Us <i></i></p>
  <h2 class="abs head about-title">Mini Excavator<br>and Earthworks for<br>Perth and Surrounds</h2>
  <p class="abs about-text">With years of experience in earthworks and site preparation, Bluegum Ridge Earthworks is committed to delivering safe, efficient, and reliable services for residential, commercial, and civil projects. Our skilled team and modern fleet ensure every job is completed on time and to the highest standard.</p>
  <div class="abs btn-dark">Learn More About Us</div>
</section>

<section>
  <p class="abs eyebrow" style="top:1736px"><i></i>Projects<i></i></p>
  <h2 class="abs head section-title" style="top:1754px">Our Recent Projects</h2>

  <div class="abs project" style="left:36px;top:1818px;background:linear-gradient(180deg,#b7c4cc,#8f7a5e 40%,#7a6248)" role="img" aria-label="Excavators digging a large foundation pit"><span class="project-tag">Project 1</span></div>
  <div class="abs project" style="left:417px;top:1818px;background:linear-gradient(180deg,#3d4a34,#6b5a40 45%,#5a4836)" role="img" aria-label="Forest land cleared for development"><span class="project-tag">Project 2</span></div>
  <div class="abs project" style="left:797px;top:1818px;background:linear-gradient(135deg,#9c8a74,#6c6660 50%,#b39070)" role="img" aria-label="Aerial view of excavator on rocky ground"><span class="project-tag">Project 3</span></div>
  <div class="abs project" style="left:36px;top:2076px;background:linear-gradient(180deg,#8ea2b2,#a0765a 55%,#8a6a52)" role="img" aria-label="City basement excavation among towers"><span class="project-tag">Project 4</span></div>
  <div class="abs project" style="left:417px;top:2076px;background:linear-gradient(180deg,#7f9c6a,#4c6e34 30%,#a38f7e 65%,#8c7466)" role="img" aria-label="Quarry excavation beside green hill"><span class="project-tag">Project 5</span></div>
  <div class="abs project" style="left:797px;top:2076px;background:linear-gradient(180deg,#a7aaa8,#77756a 45%,#9a7a5c)" role="img" aria-label="Riverside site with orange excavator"><span class="project-tag">Project 6</span></div>

  <div class="abs btn-lime">View All Projects</div>
</section>

<section>
  <div class="abs contact-lime"></div>
  <div class="abs contact-word">BLUEGUM</div>
  <div class="abs contact-lime-low"></div>
  <div class="abs contact-photo" role="img" aria-label="Site manager on phone holding a clipboard, with a road roller behind"></div>
  <h2 class="abs head contact-title">Ready to start your<br>project? Contact us<br>today for a free quote.</h2>
  <div class="abs field" style="top:2659px">Your Name Here*</div>
  <div class="abs field" style="top:2702px">Your Email Here*</div>
  <div class="abs field" style="top:2744px">Your Mobile Here*</div>
  <div class="abs field" style="top:2786px;height:88px">Your Subject Here*</div>
  <div class="abs submit">Submit</div>
</section>

<footer>
  <div class="abs site-footer"></div>
  <div class="abs brand footer-brand"><span class="brand-dot"></span>Bluegum Ridge</div>
  <p class="abs footer-about">With years of experience in earthworks and site preparation, Bluegum Ridge Earthworks is committed to delivering safe, efficient, and reliable services for residential, commercial, and civil projects.</p>
  <div class="abs footer-rule" style="left:364px"></div>
  <div class="abs footer-rule" style="left:619px"></div>
  <div class="abs footer-rule" style="left:891px"></div>

  <h4 class="abs footer-head" style="left:452px">Quick Links<i></i></h4>
  <ul class="abs footer-list" style="left:453px;top:3074px"><li>Home</li><li>About Us</li><li>Projects</li><li>Contact Us</li></ul>

  <h4 class="abs footer-head" style="left:679px">Contact Us<i></i></h4>
  <div class="abs" style="left:679px;top:3071px">
    <div class="footer-item"><span class="dot"></span>+61 400 555 218</div>
    <div class="footer-item" style="color:var(--lime)"><span class="dot"></span>info@bluegumridgeworks.com</div>
  </div>

  <h4 class="abs footer-head" style="left:965px">Follow Us<i></i></h4>
  <div class="abs" style="left:966px;top:3071px">
    <div class="footer-item"><span class="dot"></span>Social Feed</div>
    <div class="footer-item"><span class="dot"></span>Network</div>
    <div class="footer-item"><span class="dot"></span>Video Channel</div>
  </div>

  <div class="abs footer-bottom"><span>Copyright © Bluegum Ridge Earthworks. 2026 All Rights Reserved</span><span>Privacy Policy &nbsp; Terms and Conditions</span></div>
</footer>

</body>
</html>
```